New business card/stationary for a consulting company

I am looking for a clean and very professional looking business card for my consulting company as well as corresponding stationary. I am uploading our logo. I like simple and powerful for the feel. No graphics but I am open on everything else. Below is my contact information but would like the final to be in a version I can add my employees information into and print. Thank you.

Daniel Whitcombe
dan@ferncliffadvisory.com
2870 North 9th Avenue, Summit Floor, Elm Ridge, Illinois 60531
www.ferncliffadvisory.com

Industry/Entity Type

Consulting

Contact Information for Business Card

Daniel Whitcombe
dan@ferncliffadvisory.com
www.ferncliffadvisory.com

Font styles to use
Serif
Sans Serif

Requirements
Must have
• Our logo and the business card details.
Nice to have
• our website www.ferncliffadvisory.com

```html
<!DOCTYPE html>
<html lang="en">
<head>
<meta charset="utf-8">
<title>Ferncliff Advisory — Business Card</title>
<link rel="stylesheet" href="https://fonts.googleapis.com/css2?family=Montserrat:wght@400;500&family=Roboto:wght@400&display=swap">
<style>
  :root {
    --backdrop: #3a3a3c;
    --card: #262628;
    --card-edge: #1c1c1e;
    --band: #0d4a80;
    --name-blue: #1a5c9c;
    --ink-light: #ffffff;
    --mark-grey: #4a4a4e;
  }
  * { margin: 0; padding: 0; box-sizing: border-box; }
  html, body { width: 799px; height: 1200px; overflow: hidden; }
  body {
    background: var(--backdrop);
    display: flex;
    flex-direction: column;
    align-items: center;
    justify-content: center;
    gap: 150px;
  }
  .card {
    width: 620px;
    height: 354px;
    background: var(--card);
    border: 1px solid var(--card-edge);
    position: relative;
    box-shadow: 0 10px 24px rgba(0,0,0,0.35);
  }
  .card-front {
    display: flex;
    align-items: center;
    justify-content: center;
  }
  .front-name {
    font-family: "Montserrat", sans-serif;
    font-weight: 500;
    font-size: 34px;
    letter-spacing: 3px;
    color: var(--mark-grey);
    text-transform: uppercase;
  }
  .brand-band {
    position: absolute;
    left: 0;
    right: 0;
    top: 62px;
    height: 62px;
    background: var(--band);
    display: flex;
    align-items: center;
    padding-left: 30px;
    gap: 16px;
  }
  .brand-square {
    width: 22px;
    height: 22px;
    background: var(--ink-light);
  }
  .brand-name {
    font-family: "Montserrat", sans-serif;
    font-weight: 400;
    font-size: 30px;
    letter-spacing: 2px;
    color: var(--ink-light);
    text-transform: uppercase;
  }
  .contact {
    position: absolute;
    left: 150px;
    top: 152px;
  }
  .person-name {
    font-family: "Montserrat", sans-serif;
    font-weight: 400;
    font-size: 19px;
    letter-spacing: 1.5px;
    color: var(--name-blue);
    text-transform: uppercase;
    margin-bottom: 10px;
  }
  .contact-line {
    font-family: "Roboto", sans-serif;
    font-size: 16px;
    line-height: 24px;
    color: var(--ink-light);
  }
</style>
</head>
<body>
  <section class="card card-front" aria-label="Card front">
    <span class="front-name">Ferncliff Advisory</span>
  </section>

  <section class="card card-back" aria-label="Card back">
    <div class="brand-band">
      <span class="brand-square"></span>
      <span class="brand-name">Ferncliff Advisory</span>
    </div>
    <div class="contact">
      <p class="person-name">Daniel Whitcombe</p>
      <p class="contact-line">dan@ferncliffadvisory.com</p>
      <p class="contact-line">www.ferncliffadvisory.com</p>
      <p class="contact-line">2870 North 9th Avenue, Summit</p>
      <p class="contact-line">Floor, Elm Ridge, Illinois 60531</p>
    </div>
  </section>
</body>
</html>
```